Wordpress Website design partner needed for an Arabic Language Institute for English Speakers

We are an online Arabic Language institute, targeting English Speakers around the world and we provide online courses and private group and one on one classes
We are looking for a total of 5 pages designed.
The Design should be mobile-first, and then provide PC for any differences.
I am looking for a consistent design with a lot of white space and in line with our Logo colours.
Images used should be around the theme of Arabic Language/Islamic in Nature, so please do not use any illustrations or images of animals or human beings except for silhouettes or images without faces visible, such as someone facing other way or below torso or hands etc.
The website will eventually be prepared for Wordpress using Divi.
I will provide a very structured outline of what elements and modules each page should have. Therefore I am looking for someone that has an eye for detail and is precise in executing requirements.
I decided to post on this site because I am looking for a long-term partner that can take care of any of our design needs as they come up.
More details to follow
I will do abit more research tomorrow to suggest sample sites
Updates
Target Market(s)
English speakers that want to learn Arabic for Religous purposes such as understanding the Quran
Industry/Entity Type
Education
Colors
Designer to choose colors to be used in the design.
Requirements
Must have
- Mobile First, and design for PC for changes
- Consistency
- Plenty of White Space
- Colour Palette based on Logo
- Colour and Transparent/White Header for when scrolling
- Big Call to Action buttons with contrasting colors
- A consistent footer for all pages with
- -Social Media Icons
- -Contact us
- -Sitemap
- -Copyright
- -Logo
- Anything with a hashtag (#) beforehand in the Doc file means it should be a module like the modules used in Divi Theme, Please check the following website for an explanation of what each module consists of and some examples of it in use. https://www.pelmorashowcase.net/pelmora-blocks-guide/
Nice to have
- Parallax Effect
Should not have
- illustrations or images of animals or human beings except for silhouettes or images without faces visible, such as someone facing other way or below torso or hands etc.

```html
<!DOCTYPE html>
<html lang="en">
<head>
<meta charset="utf-8">
<title>Al-Manar Arabic Academy – Contact</title>
<link href="https://fonts.googleapis.com/css2?family=Poppins:wght@400;500;600;700&display=swap" rel="stylesheet">
<style>
:root{
  --brand:#0d5c9e;
  --brand-dark:#0b4f88;
  --hero-start:#1a3ce0;
  --hero-end:#6a0ad8;
  --white:#ffffff;
  --muted:#6e7a86;
  --line:#d9e3ee;
}
*{box-sizing:border-box;margin:0;padding:0}
html,body{width:1200px;height:3534px;overflow:hidden}
body{font-family:'Poppins',sans-serif;background:var(--white);color:var(--brand);position:relative}
.abs{position:absolute}

/* header */
.topbar{left:0;top:0;width:1200px;height:67px;background:var(--white)}
.brand{left:74px;top:8px;display:flex;align-items:center;gap:12px}
.brand-mark{width:52px;height:52px;background:var(--brand);border-radius:4px}
.brand-name{font-weight:600;font-size:20px;line-height:1.05;color:var(--brand);width:140px}
.top-social{right:72px;top:13px;display:flex;gap:14px}
.dot{width:28px;height:28px;border-radius:50%;background:var(--brand);display:block}
.navbar{left:0;top:67px;width:1200px;height:30px;background:var(--brand)}
.nav-item{top:5px;font-size:17px;font-weight:600;color:var(--white);text-decoration:none}

/* hero */
.hero{left:0;top:97px;width:1200px;height:878px;background:linear-gradient(90deg,var(--hero-start),var(--hero-end))}
.hero-logo{left:150px;top:310px;width:240px;height:330px;display:flex;flex-direction:column;align-items:center;justify-content:center;gap:24px}
.hero-logo .mark{width:150px;height:150px;border-radius:50%;background:rgba(255,255,255,.18)}
.hero-logo .name{color:var(--white);font-weight:600;font-size:30px;letter-spacing:5px;text-align:center;line-height:1.25}
.callback{left:566px;top:190px;width:559px;height:639px;background:var(--white)}
.callback h2{position:absolute;left:44px;top:45px;font-weight:500;font-size:41px;color:var(--brand);display:flex;align-items:center;gap:10px}
.field{position:absolute;left:44px;width:471px;height:55px;border:2px solid var(--brand);font-size:19px;color:var(--muted);padding:14px 22px}
.field.msg{height:122px}
.submit{position:absolute;left:44px;top:530px;width:271px;height:55px;background:var(--brand);color:var(--white);font-size:20px;font-weight:500;display:flex;align-items:center;justify-content:center}

/* faq */
.faq-head{left:0;top:1100px;width:1200px;text-align:center}
.faq-head .q{font-size:96px;font-weight:700;line-height:1}
.faq-head h2{font-size:42px;font-weight:500;margin-top:6px}
.faq-item{left:75px;width:1050px;height:75px;background:var(--brand);border-radius:18px;color:var(--white);font-weight:700;font-size:30px;display:flex;align-items:center;justify-content:space-between;padding:0 46px 0 52px}
.plus{width:46px;height:46px;position:relative}
.plus::before,.plus::after{content:"";position:absolute;background:var(--white)}
.plus::before{left:0;top:21px;width:46px;height:4px}
.plus::after{left:21px;top:0;width:4px;height:46px}

/* contact strip */
.contact-card{top:2086px;width:380px;display:flex;flex-direction:column;align-items:center}
.circle{width:185px;height:185px;border-radius:50%;background:var(--brand);display:flex;align-items:center;justify-content:center}
.contact-text{margin-top:18px;font-weight:700;font-size:29px;text-align:center;line-height:1.15}
.social-grid{margin-top:22px;display:flex;flex-direction:column;align-items:center;gap:8px}
.social-grid div{display:flex;gap:22px}
.social-grid .dot{width:44px;height:44px}

/* footer */
.footer{left:0;top:2660px;width:1200px;height:860px;background:var(--brand);color:var(--white)}
.footer h3{position:absolute;top:104px;font-size:25px;font-weight:500}
.footer p{position:absolute;font-size:23px;line-height:1.6}
.footer a{position:absolute;color:var(--white);font-size:21px;text-decoration:underline;text-underline-offset:5px}
.divider{position:absolute;left:118px;top:632px;width:723px;height:2px;background:var(--white)}
.foot-logo{position:absolute;left:920px;top:600px;width:120px;display:flex;flex-direction:column;align-items:center;gap:10px}
.foot-logo .mark{width:80px;height:80px;border-radius:50%;background:rgba(255,255,255,.22)}
.foot-logo span{font-weight:600;font-size:15px;letter-spacing:2px;text-align:center;line-height:1.2}
.copyright{position:absolute;left:142px;top:755px;font-size:20px;letter-spacing:1px}
.foot-social{position:absolute;left:889px;top:761px;display:flex;gap:28px}
.foot-social .dot{width:25px;height:25px;background:var(--white)}
</style>
</head>
<body>

<header class="abs topbar">
  <div class="abs brand"><span class="brand-mark"></span><span class="brand-name">AL-MANAR arabic academy</span></div>
  <div class="abs top-social" aria-label="Social links">
    <span class="dot"></span><span class="dot"></span><span class="dot"></span><span class="dot"></span><span class="dot"></span>
  </div>
</header>
<nav class="abs navbar">
  <a class="abs nav-item" style="left:72px">Home</a>
  <a class="abs nav-item" style="left:238px">About us</a>
  <a class="abs nav-item" style="left:431px">Courses</a>
  <a class="abs nav-item" style="left:619px">Pricing</a>
  <a class="abs nav-item" style="left:793px">Testimonials</a>
  <a class="abs nav-item" style="left:1023px">Contact us</a>
</nav>

<section class="abs hero">
  <div class="abs hero-logo" style="top:213px">
    <span class="mark"></span>
    <span class="name">AL-MANAR ARABIC ACADEMY</span>
  </div>
  <form class="abs callback" style="top:93px">
    <h2><svg width="38" height="38" viewBox="0 0 24 24"><path fill="#0d5c9e" d="M6.6 10.8a15.1 15.1 0 0 0 6.6 6.6l2.2-2.2c.3-.3.7-.4 1-.2 1.1.4 2.3.6 3.6.6.6 0 1 .4 1 1V20c0 .6-.4 1-1 1A17 17 0 0 1 3 4c0-.6.4-1 1-1h3.5c.6 0 1 .4 1 1 0 1.3.2 2.5.6 3.6.1.3 0 .7-.2 1z"/></svg>GET A CALBACK</h2>
    <div class="field" style="top:118px">YOUR NAME</div>
    <div class="field" style="top:204px">YOUR EMAIL ADRESS</div>
    <div class="field" style="top:290px">CONTACT NUMBER</div>
    <div class="field msg" style="top:376px">MESSAGE(OPTIONAL)</div>
    <div class="submit">SUBMIT</div>
  </form>
</section>

<section>
  <div class="abs faq-head"><div class="q">?</div><h2>FAQ’S</h2></div>
  <div class="abs faq-item" style="top:1357px">HOW WILL THE COURSE WORK’S ?<span class="plus"></span></div>
  <div class="abs faq-item" style="top:1464px">WILL I GET CERTIFIED AFTER THIS COURSE ?<span class="plus"></span></div>
  <div class="abs faq-item" style="top:1571px">WHAT IS THE AIM OF THE COURSE?<span class="plus"></span></div>
  <div class="abs faq-item" style="top:1678px">HOW WILL THE COURSE WORK’S ?<span class="plus"></span></div>
  <div class="abs faq-item" style="top:1785px">WHAT IS THE DURATION OF THE COURSE?<span class="plus"></span></div>
</section>

<section>
  <div class="abs contact-card" style="left:52px">
    <div class="circle"><svg width="100" height="76" viewBox="0 0 100 76"><rect x="2" y="2" width="96" height="72" rx="6" fill="#fff"/><path d="M4 6l46 38 46-38" fill="none" stroke="#0d5c9e" stroke-width="7"/><path d="M4 72l34-30M96 72L62 42" stroke="#0d5c9e" stroke-width="6"/></svg></div>
    <div class="contact-text">contact@almanar-academy.org/<br>info@almanar-academy.org</div>
  </div>
  <div class="abs contact-card" style="left:448px">
    <div class="circle"><svg width="90" height="90" viewBox="0 0 24 24"><path fill="#fff" d="M6.6 10.8a15.1 15.1 0 0 0 6.6 6.6l2.2-2.2c.3-.3.7-.4 1-.2 1.1.4 2.3.6 3.6.6.6 0 1 .4 1 1V20c0 .6-.4 1-1 1A17 17 0 0 1 3 4c0-.6.4-1 1-1h3.5c.6 0 1 .4 1 1 0 1.3.2 2.5.6 3.6.1.3 0 .7-.2 1z"/><path d="M14 3a7 7 0 0 1 7 7M14 6.5a3.5 3.5 0 0 1 3.5 3.5" fill="none" stroke="#fff" stroke-width="1.8"/></svg></div>
    <div class="contact-text">+91 90000 11223/<br>0240555018</div>
  </div>
  <div class="abs contact-card" style="left:844px">
    <div class="circle"><svg width="70" height="100" viewBox="0 0 70 100"><rect x="14" y="4" width="44" height="92" rx="7" fill="#fff"/><rect x="22" y="14" width="28" height="64" fill="#0d5c9e"/><circle cx="36" cy="87" r="4" fill="#0d5c9e"/></svg></div>
    <div class="social-grid" aria-label="Social links">
      <div><span class="dot"></span><span class="dot"></span></div>
      <div><span class="dot"></span><span class="dot"></span><span class="dot"></span></div>
    </div>
  </div>
</section>

<footer class="abs footer">
  <h3 style="left:148px">CONTACT US</h3>
  <h3 style="left:541px">SITEMAP</h3>
  <h3 style="left:890px">ABOUT</h3>
  <p style="left:151px;top:200px">Al-Manar academy ltd<br>(555-010-442)</p>
  <p style="left:151px;top:335px">9am - 6pm ET,<br>Monday - Friday</p>
  <p style="left:151px;top:470px">Info@Al-Manar.org</p>
  <a style="left:540px;top:200px">Home</a>
  <a style="left:540px;top:267px">About</a>
  <a style="left:540px;top:335px">Services</a>
  <a style="left:540px;top:402px">Courses</a>
  <a style="left:540px;top:470px">Features</a>
  <a style="left:892px;top:213px">FAQ</a>
  <a style="left:892px;top:281px">Contact Us</a>
  <a style="left:892px;top:348px">Demo</a>
  <a style="left:892px;top:416px">Terms of Service,</a>
  <a style="left:892px;top:483px">Privacy</a>
  <div class="divider"></div>
  <div class="foot-logo"><span class="mark"></span><span>AL-MANAR ARABIC ACADEMY</span></div>
  <div class="copyright">copyright 2019 @Al Manar academy pvt ltd.</div>
  <div class="foot-social" aria-label="Social links"><span class="dot"></span><span class="dot"></span><span class="dot"></span><span class="dot"></span></div>
</footer>

</body>
</html>
```